Brightfield Ventures Inc. Letterhead

Creation of attractive and eye catching letterhead for a business start-up for the construction industry. Letterhead must relate to construction, but avoid standard hammer and tools in the design.

I forgot to add some details, sorry about that. Some pertinent info: Ph: 916-555-0187 brightfieldventures.example 448 Willowmere Ave, Ste 210 Folsom, CA 95999 info@brightfieldventures.example not sure if slogan should be in there" “Connecting construction professionals to create a purpose driven industry.” must be able to be used in word. Thanks!

```html
<!DOCTYPE html>
<html lang="en">
<head>
<meta charset="utf-8">
<title>Brightfield Ventures Inc. Letterhead</title>
<link href="https://fonts.googleapis.com/css2?family=Lato:wght@400;700&family=Montserrat:wght@600&family=Kaushan+Script&display=swap" rel="stylesheet">
<style>
  :root {
    --navy: #1d2358;
    --red: #bd1f26;
    --ink: #555a60;
    --dark: #2a2a2a;
    --paper: #ffffff;
  }
  * { margin: 0; padding: 0; box-sizing: border-box; }
  html, body { width: 931px; height: 1200px; overflow: hidden; background: var(--paper); }
  .letterhead {
    position: relative;
    width: 931px;
    height: 1200px;
    background: var(--paper);
    font-family: "Lato", sans-serif;
  }
  .brand {
    position: absolute;
    top: 60px;
    left: 0;
    width: 100%;
    display: flex;
    flex-direction: column;
    align-items: center;
    gap: 14px;
  }
  .brand-mark {
    width: 34px;
    height: 34px;
    background: var(--red);
  }
  .brand-name {
    font-family: "Montserrat", sans-serif;
    font-weight: 600;
    font-size: 22px;
    letter-spacing: 2px;
    color: var(--navy);
    text-transform: uppercase;
  }
  .letter {
    position: absolute;
    top: 326px;
    left: 69px;
    width: 796px;
  }
  .greeting {
    font-weight: 700;
    font-size: 17px;
    color: var(--navy);
    margin-bottom: 24px;
  }
  .letter p.body {
    font-size: 17.5px;
    line-height: 29px;
    color: var(--ink);
    margin-bottom: 14px;
  }
  .closing {
    margin-top: 36px;
    font-size: 21px;
    color: var(--dark);
  }
  .signature {
    font-family: "Kaushan Script", cursive;
    font-size: 36px;
    color: var(--navy);
    margin-top: 2px;
  }
  .footer-address {
    position: absolute;
    left: 0;
    top: 1122px;
    width: 100%;
    height: 38px;
    background: var(--red);
    color: #fff;
    font-size: 14px;
    display: flex;
    align-items: center;
    justify-content: center;
    gap: 6px;
  }
  .footer-contact {
    position: absolute;
    left: 0;
    top: 1160px;
    width: 100%;
    height: 40px;
    background: var(--navy);
    color: #fff;
    font-size: 14px;
    display: flex;
    align-items: center;
    justify-content: center;
    gap: 22px;
  }
  .contact-item { display: flex; align-items: center; gap: 6px; }
  .icon { width: 12px; height: 12px; fill: none; stroke: #fff; stroke-width: 1.6; }
</style>
</head>
<body>
<div class="letterhead">
  <header class="brand">
    <div class="brand-mark"></div>
    <div class="brand-name">Brightfield Ventures Inc.</div>
  </header>

  <main class="letter">
    <p class="greeting">Dear Mr. Lorem,</p>
    <p class="body">Lorem ipsum dolor sit amet, consectetuer adipiscing elit, sed diam nonummy nibh euismod tincidunt ut laoreet dolore magna aliquam erat volutpat. Ut wisi enim ad minim veniam, quis nostrud exerci tation ullamcorper suscipit lobortis nisl ut aliquip ex ea commodo consequat. Duis autem vel eum iriure dolor in hendiusto odio dignissim qui blandit praesent luptatum zzril delenit augue duis dolore te feugait nulla facilisi.</p>
    <p class="body">Lorem ipsum dolor sit amet, consectetuer adipiscing elit, sed diam nonummy nibh euismod tincidunt ut laoreet dolore magna aliquam erat volutpat. Ut wisi enim ad minim veniam, quis nostrud exerci tation ullamcorper suscipit lobortis nisl ut aliquip ex ea commodo consequat. Duis autem vel eum iriure dolor in hendiusto odio dignissim qui blandit praesent luptatum zzril delenit augue duis dolore te feugait nulla facilisi.</p>
    <p class="body">Lorem ipsum dolor sit amet, consectetuer adipiscing elit, sed diam nonummy nibh euismod tincidunt ut laoreet dolore magna aliquam erat volutpat. Ut wisi enim ad minim veniam, quis nostrud exerci tation ullamcorper suscipit lobortis nisl ut aliquip ex ea commodo consequat. Duis autem vel eum iriure dolor in hendiusto odio dignissim qui blandit praesent luptatum zzril delenit augue duis dolore te feugait nulla facilisi.</p>
    <p class="closing">Sincerely Your,</p>
    <p class="signature">Your Name</p>
  </main>

  <footer>
    <div class="footer-address">
      <svg class="icon" viewBox="0 0 12 12" aria-hidden="true"><path d="M6 11 C3 7.5 2 6 2 4.5 A4 4 0 0 1 10 4.5 C10 6 9 7.5 6 11 Z"/><circle cx="6" cy="4.5" r="1.3"/></svg>
      <span>448 Willowmere Ave, Ste 210, Folsom, CA 95999</span>
    </div>
    <div class="footer-contact">
      <span class="contact-item">
        <svg class="icon" viewBox="0 0 12 12" aria-hidden="true"><path d="M2.5 1.5 L4.5 1.5 L5.3 4 L4 5 C4.7 6.5 5.5 7.3 7 8 L8 6.7 L10.5 7.5 L10.5 9.5 C10.5 10 10 10.5 9.5 10.5 C5.5 10.3 1.7 6.5 1.5 2.5 C1.5 2 2 1.5 2.5 1.5 Z"/></svg>
        916-555-0187
      </span>
      <span class="contact-item">
        <svg class="icon" viewBox="0 0 12 12" aria-hidden="true"><rect x="1.5" y="3" width="9" height="6.5"/><path d="M1.5 3 L6 6.5 L10.5 3"/></svg>
        info@brightfieldventures.example
      </span>
      <span class="contact-item">
        <svg class="icon" viewBox="0 0 12 12" aria-hidden="true"><circle cx="6" cy="6" r="4.6"/><ellipse cx="6" cy="6" rx="2" ry="4.6"/><path d="M1.4 6 H10.6"/></svg>
        brightfieldventures.example
      </span>
    </div>
  </footer>
</div>
</body>
</html>
```